Harbor Ledger Funds Bus card and Logo

I need a logo design and Bus card design. The fund focuses on evaluating and investing in minerals (sub-surface rights) and real estate.

Harbor ledger refers to a book of knowledge that each plebe gets when entering the Kelmont Marine Academy (my alma mater)

Target Market(s)

Investors and financial advisors

Contact Information for Business Card

Simple - perhaps a logo with a theme on book of knowledge

Logo Text

Ex Scientia Imperium

Font styles to use
Serif
Sans Serif

Colors

Designer to choose colors to be used in the design.

Requirements
Must have
• memorable logo that is relatively simple

```html
<!DOCTYPE html>
<html lang="en">
<head>
<meta charset="UTF-8">
<title>Harbor Ledger Funds – Business Card</title>
<link rel="stylesheet" href="https://fonts.googleapis.com/css2?family=Roboto:wght@500&family=Open+Sans:wght@400;600&display=swap">
<style>
  :root {
    --backdrop: #2f2f2f;
    --card-light: #ededed;
    --brand-green: #8cc63f;
    --brand-blue: #3399d1;
    --brand-teal: #45a6b4;
    --ink: #1e1e1e;
    --rule: #9a9a9a;
    --white: #ffffff;
  }
  html, body {
    margin: 0;
    padding: 0;
    width: 1200px;
    height: 1200px;
    overflow: hidden;
    background: var(--backdrop);
  }
  .canvas {
    position: relative;
    width: 1200px;
    height: 1200px;
  }
  .card {
    position: absolute;
    top: 310px;
    height: 594px;
    box-sizing: border-box;
  }
  .card-front {
    left: 234px;
    width: 364px;
    background: var(--card-light);
    text-align: center;
    font-family: "Open Sans", Arial, sans-serif;
    color: var(--ink);
  }
  .card-back {
    left: 627px;
    width: 369px;
    background:
      radial-gradient(ellipse 75% 60% at 50% 52%, #8cc63f 0%, #86c442 45%, rgba(134,196,66,0) 100%),
      linear-gradient(160deg, #6cba6a 0%, #45a6b4 8%, #7bc25a 40%, #86c442 60%, #5fb07a 88%, #45a6b4 100%);
    text-align: center;
  }
  .brand-mark {
    position: absolute;
    left: 0;
    right: 0;
    display: flex;
    flex-direction: column;
    align-items: center;
  }
  .brand-dot {
    border-radius: 50%;
  }
  .brand-name {
    font-family: "Roboto", Arial, sans-serif;
    font-weight: 500;
    text-transform: uppercase;
    line-height: 1.1;
  }
  .card-front .brand-mark { top: 110px; }
  .card-front .brand-dot {
    width: 96px; height: 96px;
    background: var(--brand-green);
  }
  .card-front .brand-name {
    margin-top: 26px;
    font-size: 25px;
    color: var(--brand-blue);
  }
  .card-back .brand-mark { top: 190px; }
  .card-back .brand-dot {
    width: 100px; height: 100px;
    background: var(--white);
  }
  .card-back .brand-name {
    margin-top: 42px;
    font-size: 36px;
    color: var(--white);
  }
  .holder {
    position: absolute;
    top: 345px;
    left: 0;
    right: 0;
  }
  .holder-name {
    font-family: "Roboto", Arial, sans-serif;
    font-weight: 500;
    font-size: 21px;
    color: var(--brand-green);
    margin: 0;
    line-height: 24px;
  }
  .holder-role {
    font-size: 17px;
    margin: 0;
    line-height: 22px;
  }
  .rule {
    width: 208px;
    height: 1px;
    background: var(--rule);
    margin: 0 auto;
    border: 0;
  }
  .rule-top { margin-top: 7px; }
  .contact {
    list-style: none;
    padding: 0;
    margin: 8px 0 12px;
    font-size: 17px;
    line-height: 21.5px;
  }
  .contact .label { color: var(--brand-green); }
  .contact .web { color: var(--brand-green); }
  .contact .web .domain { color: var(--brand-blue); }
  .address {
    margin: 7px 0 0;
    font-size: 17px;
    line-height: 21.5px;
    font-style: normal;
  }
</style>
</head>
<body>
<main class="canvas">
  <section class="card card-front">
    <div class="brand-mark">
      <span class="brand-dot" aria-hidden="true"></span>
      <span class="brand-name">Harbor Ledger Funds</span>
    </div>
    <div class="holder">
      <p class="holder-name">DANIEL MORROW</p>
      <p class="holder-role">Managing Director</p>
      <hr class="rule rule-top">
      <ul class="contact">
        <li><span class="label">P:</span> 055-987 654 321</li>
        <li><span class="label">M:</span> 055-987 654 321</li>
        <li><span class="label">E:</span> info@harborledger.com</li>
        <li class="web">www.<span class="domain">harborledgerfunds</span>.com</li>
      </ul>
      <hr class="rule">
      <address class="address">48, Quay Street Lane<br>Port Alden, 204518.</address>
    </div>
  </section>
  <section class="card card-back">
    <div class="brand-mark">
      <span class="brand-dot" aria-hidden="true"></span>
      <span class="brand-name">Harbor Ledger<br>Funds</span>
    </div>
  </section>
</main>
</body>
</html>
```